Brindle Yard Care. The best in the biz

I run a lawn care service that offers full service mowing. 100% satisfaction guarantee. Fast, Friendly, quality service "I am your lawns best friend" I cut residential lawns. I offer a mow package that includes trimming, edging and clean up. Prices very from 20 dollars to 75. I want my logo to stand out. Free estimates

Target Market(s)

Home owners

Industry/Entity Type

Landscaping

Contact Information for Business Card

555-812-4473 tomvale48@quillmail.net Derek. Brindle Yard care

Colors
f37122
9bcb3c
cadf82

Requirements
Must have
• Company name.
• Phone number
• Email
• My services
• images
Nice to have
• A sun that is growing grass.
Should not have
• Incorrect information

```html
<!DOCTYPE html>
<html lang="en">
<head>
<meta charset="utf-8">
<title>Brindle Yard Care – Business Card</title>
<link rel="stylesheet" href="https://fonts.googleapis.com/css2?family=Open+Sans:wght@400;600;800&display=swap">
<style>
  :root {
    --backdrop: #ebe7e1;
    --card: #ffffff;
    --ink: #1d1d1b;
    --leaf: #9bcb3c;
    --leaf-soft: #cadf82;
    --icon-box: #1f1f1f;
  }
  * { box-sizing: border-box; margin: 0; padding: 0; }
  html, body {
    width: 1200px; height: 902px; overflow: hidden;
    background: var(--backdrop);
    font-family: "Open Sans", Arial, sans-serif;
    color: var(--ink);
  }
  .business-card {
    position: absolute; left: 60px; top: 143px;
    width: 1080px; height: 615px;
    background: var(--card);
    box-shadow: 0 6px 24px rgba(0,0,0,.15);
    overflow: hidden;
  }
  .brand {
    position: absolute; left: 77px; top: 205px; width: 400px;
  }
  .brand-name {
    display: flex; align-items: center; gap: 14px;
    color: var(--leaf); font-weight: 800; font-size: 58px; line-height: 1;
    letter-spacing: -0.5px;
  }
  .brand-mark {
    width: 28px; height: 28px; border-radius: 50%;
    background: var(--leaf); flex: none;
  }
  .brand-name-lines { display: block; }
  .brand-name-lines span { display: block; }
  .tagline {
    position: absolute; left: 147px; top: 398px;
    font-size: 25px; font-weight: 400; white-space: nowrap;
  }
  .divider {
    position: absolute; left: 540px; top: 139px;
    width: 2px; height: 336px; background: var(--leaf-soft);
  }
  .contact { position: absolute; left: 586px; top: 0; }
  .contact-name {
    position: absolute; top: 162px; font-size: 36px; font-weight: 600; white-space: nowrap;
  }
  .contact-line {
    position: absolute; display: flex; align-items: center; gap: 12px;
    font-size: 27px; white-space: nowrap;
  }
  .contact-line.phone { top: 295px; }
  .contact-line.email { top: 332px; }
  .contact-icon { width: 27px; height: 27px; flex: none; }
  .promise {
    position: absolute; top: 392px; font-size: 27px; line-height: 37px; white-space: nowrap;
  }
  .grass-band {
    position: absolute; left: 0; bottom: 0; width: 100%; height: 135px;
    background: linear-gradient(to bottom, rgba(202,223,130,0) 0%, var(--leaf-soft) 45%, var(--leaf) 100%);
  }
</style>
</head>
<body>
  <main class="business-card">
    <div class="brand">
      <div class="brand-name">
        <span class="brand-mark"></span>
        <span class="brand-name-lines"><span>Brindle</span><span>Yard care</span></span>
      </div>
    </div>
    <p class="tagline">I am your lawns best friend</p>

    <div class="divider"></div>

    <section class="contact">
      <h1 class="contact-name">Derek Brindle</h1>
      <p class="contact-line phone">
        <svg class="contact-icon" viewBox="0 0 24 24" aria-hidden="true">
          <rect width="24" height="24" fill="var(--icon-box)"/>
          <path d="M7 4.5l3 3-1.6 2.2c1.2 2.4 3.2 4.4 5.6 5.6l2.2-1.6 3 3-2 2.8C11 19 5 13 4.2 6.5z" fill="var(--leaf)"/>
        </svg>
        555-812-4473
      </p>
      <p class="contact-line email">
        <svg class="contact-icon" viewBox="0 0 24 24" aria-hidden="true">
          <rect width="24" height="24" fill="var(--icon-box)"/>
          <rect x="4" y="6.5" width="16" height="11" fill="var(--leaf)"/>
          <path d="M4 6.5l8 6.5 8-6.5M4 17.5l6-5.5M20 17.5l-6-5.5" fill="none" stroke="var(--icon-box)" stroke-width="1.3"/>
        </svg>
        tomvale48@quillmail.net
      </p>
      <p class="promise">100% satisfaction guarantee<br>Fast, Friendly, quality service</p>
    </section>

    <div class="grass-band" role="img" aria-label="Illustration of a strip of green grass blades along the bottom edge"></div>
  </main>
</body>
</html>
```